Boutique custom software development company needs new business card

Our nearly 20 year old custom software development company would like to better include the fact that we are now providing Bitcoin services. These new services are B2B include education (how to acquire and securely hold Bitcoin) and integrating Bitcoin payments into existing ecommerce sites or other existing systems. Please keep the card clean and simple. Attached is our current design and some other files. vextorial.com

Target Market(s)

businesses owners interested in long term relationship

Industry/Entity Type

Custom software development and Bitcoin

Contact Information for Business Card

Dale Parker, dale@vextorial.com, vextorial.com, (888) 555-VXTRL

Font styles to use
Other font styles liked:
• monospace

Requirements
Must have
• double-sided
Nice to have
• clean and simple
Should not have
• physical address

```html
<!DOCTYPE html>
<html lang="en">
<head>
<meta charset="utf-8">
<title>Vextorial business card</title>
<link href="https://fonts.googleapis.com/css2?family=Titillium+Web:wght@300;700&family=Arimo:wght@400;700&display=swap" rel="stylesheet">
<style>
  :root {
    --brand-blue: #3a6cb0;
    --brand-orange: #e87722;
    --card-white: #f6f6f6;
    --stage: #d9d9d9;
    --ink-light: #ffffff;
  }
  * { margin: 0; padding: 0; box-sizing: border-box; }
  html, body { width: 1200px; height: 912px; overflow: hidden; }
  body {
    background: var(--stage);
    display: flex;
    flex-direction: column;
    align-items: center;
    justify-content: center;
    gap: 32px;
  }
  .card {
    position: relative;
    width: 700px;
    height: 400px;
    overflow: hidden;
    box-shadow: 0 4px 14px rgba(0,0,0,0.18);
  }

  /* Front side */
  .card-front { background: var(--card-white); }
  .brand-block {
    position: absolute;
    left: 150px;
    top: 120px;
  }
  .brand-name {
    font-family: "Titillium Web", sans-serif;
    font-weight: 700;
    font-size: 92px;
    line-height: 1;
    letter-spacing: 1px;
    color: var(--brand-blue);
  }
  .brand-tagline {
    font-family: "Titillium Web", sans-serif;
    font-weight: 300;
    font-size: 31px;
    line-height: 1.1;
    color: var(--brand-blue);
    margin-top: 4px;
  }
  .front-url {
    position: absolute;
    right: 120px;
    bottom: 62px;
    font-family: "Arimo", sans-serif;
    font-weight: 700;
    font-size: 16px;
    letter-spacing: 1.5px;
    color: var(--brand-blue);
  }
  .front-url .url-name { color: var(--brand-orange); }

  /* Back side */
  .card-back { background: var(--brand-blue); }
  .corner-accent {
    position: absolute;
    left: 0;
    bottom: 0;
  }
  .holder {
    position: absolute;
    right: 52px;
    top: 52px;
    text-align: right;
    color: var(--ink-light);
    font-family: "Arimo", sans-serif;
  }
  .holder-name { font-weight: 700; font-size: 36px; line-height: 1.05; }
  .holder-role { font-weight: 400; font-size: 21px; margin-top: 2px; }
  .contact-list {
    position: absolute;
    right: 52px;
    top: 232px;
    list-style: none;
    font-family: "Arimo", sans-serif;
    font-size: 20px;
    color: var(--ink-light);
    text-align: right;
  }
  .contact-list li {
    display: flex;
    justify-content: flex-end;
    align-items: center;
    gap: 8px;
    line-height: 28px;
  }
  .contact-icon { width: 14px; height: 14px; flex: none; }
</style>
</head>
<body>

  <section class="card card-front" aria-label="Card front">
    <div class="brand-block">
      <div class="brand-name">Vextorial</div>
      <div class="brand-tagline">developer of custom applications</div>
    </div>
    <div class="front-url">www.<span class="url-name">vextorial</span>.com</div>
  </section>

  <section class="card card-back" aria-label="Card back">
    <svg class="corner-accent" width="300" height="220" viewBox="0 0 300 220" aria-hidden="true">
      <polygon points="0,30 240,220 0,220" fill="var(--brand-orange)"/>
    </svg>

    <div class="holder">
      <div class="holder-name">Dale Parker</div>
      <div class="holder-role">Bitcoin educator</div>
    </div>

    <ul class="contact-list">
      <li>(888) 555-VXTRL
        <svg class="contact-icon" viewBox="0 0 14 14" aria-hidden="true">
          <path d="M3 1 L5 1 L6 4 L4.5 5.2 Q6 8.5 8.8 9.5 L10 8 L13 9 L13 11 Q12.5 13 10.5 13 Q2 11.5 1 3.5 Q1 1.5 3 1 Z" fill="var(--ink-light)"/>
        </svg>
      </li>
      <li>dale@vextorial.com
        <svg class="contact-icon" viewBox="0 0 14 14" aria-hidden="true">
          <rect x="0.5" y="3" width="13" height="9" fill="var(--ink-light)"/>
          <path d="M0.5 3 L7 8 L13.5 3" fill="none" stroke="var(--brand-blue)" stroke-width="1.2"/>
        </svg>
      </li>
      <li>www.vextorial.com
        <svg class="contact-icon" viewBox="0 0 14 14" aria-hidden="true">
          <circle cx="7" cy="7" r="6.5" fill="var(--ink-light)"/>
          <ellipse cx="7" cy="7" rx="2.6" ry="6.5" fill="none" stroke="var(--brand-blue)" stroke-width="1"/>
          <line x1="0.5" y1="7" x2="13.5" y2="7" stroke="var(--brand-blue)" stroke-width="1"/>
        </svg>
      </li>
    </ul>
  </section>

</body>
</html>
```